Flat bootstrap design for existing site

I'm looking for a modern flat design based around an existing logo. This has to be a custom design (no external templates), and implemented into a bootstrap framework.

The logo is attached as 2 versions - choose whichever you want, that flows better with whatever design you choose.

Added screenshots of the existing site (currently using the default bootstrap layouts). Please make your designs around those pages in the screenshots (i.e. the homepage only has the postal code input and the header). The active page has 3 screenshots, because I wanted to illustrate the other states that would be visible (in the table rows).

This is a moving/junk removal website, just for some context.

Here's some example websites (flat designs) that I like, just to give you an idea of what I'm after.

https://www.plimvora.com/
https://dacklow.com/
https://trevanu.com/
https://quobrintal.com/en/

Coding

Coded - Design and coding required

Number of Pages Required

5+ page

Colors

Designer to choose colors to be used in the design.

Requirements
Must have
• It must be a modern/simple flat design, that is built around the existing logo (attached).
• It has to be implemented using bootstrap.

```html
<!DOCTYPE html>
<html lang="en">
<head>
<meta charset="utf-8">
<title>Carvexo — Booking</title>
<link href="https://fonts.googleapis.com/css2?family=Roboto:wght@400;500;700&display=swap" rel="stylesheet">
<style>
:root{
  --brand:#4bc8f4;
  --brand-dark:#3cb7e3;
  --alert:#8fdcf7;
  --page:#f7f7f7;
  --panel:#ffffff;
  --line:#e2e2e2;
  --text:#6b6b6b;
  --muted:#888888;
  --thead:#8a8a8a;
  --ok:#78b15c;
  --pay:#3f7cb8;
  --wait:#666666;
  --foot:#5c5c5c;
}
*{box-sizing:border-box;margin:0;padding:0}
html,body{width:1200px;height:1089px;overflow:hidden}
body{background:var(--page);font-family:"Roboto",sans-serif;color:var(--text);position:relative}
.site-header{height:88px;background:var(--brand);position:relative}
.brand{position:absolute;left:86px;top:26px;display:flex;align-items:center;gap:10px;color:#fff;font-weight:700;font-size:30px;letter-spacing:1px}
.brand-dot{width:22px;height:22px;border-radius:50%;background:#fff}
.main-nav{position:absolute;right:86px;top:0;height:88px;display:flex}
.main-nav a{color:#fff;text-decoration:none;font-size:12.5px;font-weight:500;height:88px;line-height:88px;padding:0 29px}
.main-nav a.active{background:var(--brand-dark)}
.main-nav .account{display:flex;align-items:center;gap:26px;padding-right:14px}
.caret{width:0;height:0;border-left:4px solid transparent;border-right:4px solid transparent;border-top:5px solid #fff}
.panel{position:absolute;left:86px;top:150px;width:1029px;height:344px;background:var(--panel);border:1px solid var(--line);border-radius:3px}
.panel-title{height:63px;border-bottom:1px solid #eee;padding:0 17px;line-height:66px;font-size:15.5px;font-weight:500;color:#5f5f5f}
.field-label{position:absolute;font-size:14px;font-weight:500;color:#6f6f6f}
.input{position:absolute;height:41px;border:1px solid #ddd;border-radius:3px;background:#fff;font-size:12.5px;color:#555;padding-left:13px;line-height:40px}
.input .addon{position:absolute;right:0;top:0;width:39px;height:39px;border-left:1px solid #ddd;background:#f7f7f7;display:flex;align-items:center;justify-content:center}
.btn-update{position:absolute;left:16px;top:279px;width:106px;height:39px;background:var(--brand);color:#fff;border:0;border-radius:3px;font:500 14px "Roboto",sans-serif}
.section-title{position:absolute;left:87px;top:533px;font-size:15.5px;font-weight:500;color:#5f5f5f}
.notice{position:absolute;left:86px;top:567px;width:1028px;height:53px;background:var(--alert);border-radius:3px;color:#fff;font-size:12.5px;font-weight:500;padding-left:22px;line-height:53px}
.drivers{position:absolute;left:86px;top:655px;width:1029px;border-collapse:collapse;background:#fff;border:1px solid var(--line)}
.drivers th{background:var(--thead);color:#fff;font-size:12.5px;font-weight:500;text-align:left;height:54px;padding-left:25px;width:206px;border-right:1px solid #9a9a9a}
.drivers td{height:63px;border-top:1px solid var(--line);border-right:1px solid var(--line);padding-left:27px;font-size:14px;color:var(--muted)}
.drivers td.status{padding-left:0;text-align:center}
.badge{display:inline-block;width:128px;height:33px;line-height:33px;color:#fff;font-size:12px;font-weight:500;text-align:center}
.badge.accepted{background:var(--ok)}
.badge.sent{background:var(--brand)}
.badge.pending{background:var(--wait)}
.badge.pay{background:var(--pay)}
.site-footer{position:absolute;left:0;top:1020px;width:1200px;height:69px;background:var(--foot);color:#fff}
.copyright{position:absolute;left:87px;top:27px;font-size:12px;font-weight:500}
.social{position:absolute;left:942px;top:19px;display:flex;gap:5px}
.social span{width:30px;height:30px;border:1.5px solid #fff;border-radius:50%}
</style>
</head>
<body>
<header class="site-header">
  <div class="brand"><span class="brand-dot"></span>CARVEXO</div>
  <nav class="main-nav">
    <a href="#">BOOK</a>
    <a href="#">HOW IT WORKS</a>
    <a href="#" class="active">BECOME A DRIVER</a>
    <a href="#" class="account">mara@vantelo.com <span class="caret"></span></a>
  </nav>
</header>

<section class="panel">
  <h2 class="panel-title">BOOKING DETAILS</h2>
  <label class="field-label" style="left:18px;top:78px">Package Selected :</label>
  <div class="input" style="left:16px;top:106px;width:484px">Package 1
    <span class="addon"><svg width="8" height="12" viewBox="0 0 8 12"><path d="M4 0 8 5H0z M4 12 0 7h8z" fill="#666"/></svg></span>
  </div>
  <label class="field-label" style="left:532px;top:78px">Pick-up time selected :</label>
  <div class="input" style="left:529px;top:106px;width:485px">July 18 at 0:13 am
    <span class="addon"><svg width="12" height="12" viewBox="0 0 12 12"><rect x="0.5" y="1.5" width="11" height="10" fill="none" stroke="#666"/><rect x="0.5" y="1.5" width="11" height="2.5" fill="#666"/><path d="M2 6h8M2 8h8M2 10h8M4 4v7M6 4v7M8 4v7" stroke="#666" stroke-width=".6"/></svg></span>
  </div>
  <label class="field-label" style="left:18px;top:171px">Description :</label>
  <div class="input" style="left:16px;top:199px;width:992px;height:62px;line-height:1;padding-top:13px">1 Large Stove</div>
  <button class="btn-update">UPDATE</button>
</section>

<h2 class="section-title">DRIVERS IN YOUR AREA</h2>
<div class="notice">Please stey on this page and be patient,while we contact the drivers and find your one ASAP.</div>

<table class="drivers">
  <thead><tr><th>NAME</th><th>DISTANCE (KM)</th><th>AGREED PICK-UP TIME</th><th></th><th></th></tr></thead>
  <tbody>
    <tr><td>Perrin Vale</td><td>4.04km away</td><td>July 18at 4.13am</td><td class="status"><span class="badge accepted">TIME ACCEPTED</span></td><td class="status"><span class="badge pay">MAKE PAYMENT</span></td></tr>
    <tr><td>Dorian Mek</td><td>5.7km away</td><td>-</td><td class="status"><span class="badge sent">REQUEST SENT</span></td><td></td></tr>
    <tr><td>Calder Roan</td><td>11.13km away</td><td>-</td><td class="status"><span class="badge sent">REQUEST SENT</span></td><td></td></tr>
    <tr><td>Nilo Brecker</td><td>11.91km away</td><td>-</td><td class="status"><span class="badge pending">PENDING</span></td><td></td></tr>
  </tbody>
</table>

<footer class="site-footer">
  <p class="copyright">© Copyright 2017 Carvexo.All Rights Reserved.</p>
  <div class="social"><span></span><span></span><span></span><span></span><span></span></div>
</footer>
</body>
</html>
```